Whitcombe Business Card Design

The name of the business is Dario Whitcombe, CPA LLC
The service that we offer is Accounting, Tax & Consulting Services. I need it to have the following items:
Dario Whitcombe, Principal
Phone Number
Email Address
Physical Address

I have attached the company logo, one in black and one in white. Please provide a design in black background and the other in white background. Please include "Accounting, Tax & Consulting Services". I want the business card to be clean and very professional.

```html
<!DOCTYPE html>
<html lang="en">
<head>
<meta charset="utf-8">
<title>Dario Whitcombe, CPA LLC — Business Card</title>
<link href="https://fonts.googleapis.com/css2?family=Montserrat:wght@400;500;600;700&display=swap" rel="stylesheet">
<style>
  :root{
    --stage:#161616;
    --card:#232323;
    --red:#a01e22;
    --grey:#6f6f6f;
    --grey-light:#8c8c8c;
    --white:#f2f2f2;
  }
  *{margin:0;padding:0;box-sizing:border-box}
  html,body{width:1200px;height:927px;overflow:hidden;background:var(--stage);font-family:"Montserrat",Arial,sans-serif}
  .canvas{position:relative;width:1200px;height:927px}
  .card{position:absolute;width:560px;height:320px;background:var(--card);border-radius:22px;overflow:hidden;box-shadow:0 10px 30px rgba(0,0,0,.5)}
  .card--front{left:70px;top:100px}
  .card--back{left:570px;top:507px}

  .brand{display:flex;align-items:center;gap:12px}
  .brand__square{width:22px;height:22px;background:var(--red)}
  .brand__name{font-weight:500;color:var(--grey-light);letter-spacing:.04em;text-transform:uppercase}

  .front__lockup{position:absolute;left:70px;top:102px}
  .front__lockup .brand__name{font-size:23px}
  .front__title{margin-top:10px;font-size:19px;font-weight:600;letter-spacing:.14em;color:var(--grey-light)}
  .front__services{margin-top:18px;font-size:15px;font-weight:700;color:var(--grey)}

  .back__person{position:absolute;right:34px;top:40px;font-size:19px;font-weight:700;color:var(--red);text-transform:uppercase}
  .back__lockup{position:absolute;left:34px;top:112px}
  .back__lockup .brand__square{width:14px;height:14px}
  .back__lockup .brand__name{font-size:14px}
  .back__lockup .front__title{font-size:11px;margin-top:6px;letter-spacing:.12em;color:var(--grey)}
  .back__address{position:absolute;right:34px;top:118px;font-size:15px;line-height:1.7;color:var(--white);text-align:right}

  .contact{position:absolute;left:0;bottom:24px;list-style:none}
  .contact__item{display:flex;align-items:center;height:34px;margin-top:6px}
  .contact__tab{width:70px;height:30px;background:var(--red);border-radius:0 10px 10px 0;display:flex;align-items:center;justify-content:center}
  .contact__tab svg{width:16px;height:16px;fill:var(--white)}
  .contact__text{margin-left:16px;font-size:15px;color:var(--white)}
</style>
</head>
<body>
<main class="canvas">

  <section class="card card--front" aria-label="Card front">
    <div class="front__lockup">
      <div class="brand">
        <span class="brand__square"></span>
        <span class="brand__name">Dario Whitcombe, CPA LLC</span>
      </div>
      <p class="front__title">CERTIFIED PUBLIC ACCOUNTANT</p>
      <p class="front__services">Accounting, Tax &amp; Consulting Services</p>
    </div>
  </section>

  <section class="card card--back" aria-label="Card back">
    <h1 class="back__person">Dario Whitcombe, Principal</h1>

    <div class="back__lockup">
      <div class="brand">
        <span class="brand__square"></span>
        <span class="brand__name">Dario Whitcombe, CPA LLC</span>
      </div>
      <p class="front__title">CERTIFIED PUBLIC ACCOUNTANT</p>
    </div>

    <address class="back__address" style="font-style:normal">
      Larkfield Plaza 2800 Bay<br>
      Marlow Ave NE Suite 310
    </address>

    <ul class="contact">
      <li class="contact__item">
        <span class="contact__tab"><svg viewBox="0 0 24 24" aria-hidden="true"><path d="M6.6 10.8a15.1 15.1 0 0 0 6.6 6.6l2.2-2.2c.3-.3.7-.4 1-.2 1.1.4 2.3.6 3.6.6.6 0 1 .4 1 1V20c0 .6-.4 1-1 1A17 17 0 0 1 3 4c0-.6.4-1 1-1h3.5c.6 0 1 .4 1 1 0 1.3.2 2.5.6 3.6.1.3 0 .7-.2 1z"/></svg></span>
        <span class="contact__text">412-730-2196</span>
      </li>
      <li class="contact__item">
        <span class="contact__tab"><svg viewBox="0 0 24 24" aria-hidden="true"><path d="M2 5h20v14H2zm2 2v.5l8 5 8-5V7l-8 5z"/></svg></span>
        <span class="contact__text">info@dariowhitcombecpallc.com</span>
      </li>
      <li class="contact__item">
        <span class="contact__tab"><svg viewBox="0 0 24 24" aria-hidden="true"><path d="M12 2a10 10 0 1 0 0 20 10 10 0 0 0 0-20zm0 2c1.2 1.4 2 3.4 2.3 6H9.7C10 7.4 10.8 5.4 12 4zM4.1 13h3.6c.1 2.2.7 4.2 1.6 5.7A8 8 0 0 1 4.1 13zm3.6-3H4.1a8 8 0 0 1 5.2-5.7C8.4 5.8 7.8 7.8 7.7 10zm4.3 10c-1.2-1.4-2-3.4-2.3-7h4.6c-.3 3.6-1.1 5.6-2.3 7zm2.7-1.3c.9-1.5 1.5-3.5 1.6-5.7h3.6a8 8 0 0 1-5.2 5.7zM16.3 10c-.1-2.2-.7-4.2-1.6-5.7A8 8 0 0 1 19.9 10z"/></svg></span>
        <span class="contact__text">www.dariowhitcombecpallc.com</span>
      </li>
    </ul>
  </section>

</main>
</body>
</html>
```